Marlowe Group needs a business card

I would like the card to be simple but modern and elegant.
I like black and white.
or black and gold.
we are a private finance lender and also are involved in property and property developments.

please look at the business card photos i provided i would like M.G only one one side and all the other details on the other side use fonts that tie in with my theme.

Industry/Entity Type

Finance

Contact Information for Business Card

Marlowe Group (M.G) Daniel Marlowe M: 0413586207 E: danmarl@inboxmail.test

Font styles to use
Other font styles liked:
• Use fonts that would reflect our business

Colors
000000
ffffff

Requirements
Must have
• one side of details
• other side has either M.G or Marlowe Group like in the photos provided

```html
<!DOCTYPE html>
<html lang="en">
<head>
<meta charset="utf-8">
<title>Marlowe Group – Business Card</title>
<link rel="stylesheet" href="https://fonts.googleapis.com/css2?family=Montserrat:wght@400;500;600&display=swap">
<style>
  :root {
    --backdrop: #2a2a2c;
    --card-black: #0d0d0e;
    --card-edge: #1c1c1e;
    --gold: #d8c489;
    --gold-soft: #b9a56c;
  }
  * { margin: 0; padding: 0; box-sizing: border-box; }
  html, body {
    width: 1200px;
    height: 786px;
    overflow: hidden;
    background: var(--backdrop);
    font-family: "Montserrat", Arial, sans-serif;
  }
  .card-set {
    position: absolute;
    inset: 0;
    display: flex;
    align-items: center;
    justify-content: center;
    gap: 40px;
  }
  .card {
    position: relative;
    width: 520px;
    height: 317px;
    background: linear-gradient(135deg, #151516 0%, var(--card-black) 60%);
    border: 1px solid var(--card-edge);
    box-shadow: 0 18px 40px rgba(0, 0, 0, 0.45);
  }
  .card--details {
    padding: 0 0 0 44px;
    display: flex;
    flex-direction: column;
    justify-content: flex-end;
    padding-bottom: 40px;
    color: var(--gold);
  }
  .holder-name {
    font-weight: 600;
    font-size: 19px;
    line-height: 1.25;
    letter-spacing: 0.3px;
  }
  .rule {
    width: 92px;
    height: 1px;
    background: var(--gold-soft);
    margin: 16px 0;
  }
  .contact-list {
    list-style: none;
    font-size: 12px;
    line-height: 1.7;
    letter-spacing: 0.4px;
    font-weight: 400;
  }
  .contact-label { margin-right: 6px; }
  .company-line {
    font-size: 11px;
    font-weight: 500;
    letter-spacing: 0.4px;
  }
  .card--brand {
    display: flex;
    align-items: center;
    justify-content: center;
  }
  .brand-name {
    color: var(--gold);
    font-size: 34px;
    font-weight: 500;
    letter-spacing: 0.5px;
  }
</style>
</head>
<body>
  <main class="card-set">
    <section class="card card--details" aria-label="Card front with contact details">
      <h1 class="holder-name">Daniel<br>Marlowe</h1>
      <div class="rule"></div>
      <ul class="contact-list">
        <li><span class="contact-label">M.</span>0413586207</li>
        <li><span class="contact-label">E.</span>danmarl@inboxmail.test</li>
      </ul>
      <div class="rule"></div>
      <p class="company-line">Marlowe Group</p>
    </section>
    <section class="card card--brand" aria-label="Card back with company name">
      <p class="brand-name">Marlowe Group</p>
    </section>
  </main>
</body>
</html>
```